Tovin Brightway Website Design

About The Client:
Tovin Brightway is a sugar-free foods chain store providing services to Diabetics. They focus on the China domestic market. They describe themselves as being the 3rd space for Diabetics, the space between hospital and the home that help improve the quality of life for people wit Diabetes (see attached infographics).

They regularly hold education and advice events throughout the China. Tovin Brightway distribute a wide product range of food that is suitable for diabetic people. Tovin Brightway operate as a Franchise, providing business development services and Industry knowledge. They are actively seeking business partnerships at present.

The Brief:
Design a Home page and secondary information page(PSD only no code) that communicates our company services and company philosophy(3rd Space).
The final design should communicate 'Health, Social Responsibility and Professionalism'.
Colour scheme should orientate around Blue and White, see attached logo.

Websites we like:

http://lumo.vextaran.com/home/

https://www.pondrelix.com/

http://gate.zt.com/

Hello all, the client has advised us that he want to display the professional advice service available for diabetic people more so than a food distributor. The client is also hoping to use his website as a marketing platform to attract affiliates and build partnerships as part of Tovin Brightway's business expansion strategy.

So can you make the page more corporate, reliable and professional. Use images of experts/doctors interacting with patients and also training/knowledge transfer images.

Thanks

Hello all, could you include stock images of both Chinese and Caucasians

Yeaahhh, Infographics and photos have been uploaded. Feel free to use them in your designs and also as references.

Target Market(s)

The target market is Chinese B2B in the Diabetics industry and Entrepreneurs looking to cooperate with Tovin Brightway.

Industry/Entity Type

Education

Requirements
Must have
• menu navigation with 7-8 sections,
a full screen background image,
Social Media icons,
Logo in top left,
Site search.
Nice to have
• The website must be clear and easy to use, less complicated.

See attached files of some Tovin Brightway infographics. Feel free to include elements of these into the design.
Should not have
• Should not use stock images of people from any other country, the client wants stock images of Chinese people only. Avoid photos showing obesity.

```html
<!DOCTYPE html>
<html lang="en">
<head>
<meta charset="utf-8">
<title>Tovin Brightway – Home</title>
<link href="https://fonts.googleapis.com/css2?family=Open+Sans:ital,wght@0,400;0,600;0,700;1,400;1,600&display=swap" rel="stylesheet">
<style>
:root{
  --blue:#1f6db3;
  --blue-dark:#17558f;
  --blue-light:#3aa7d9;
  --sky:#e9f3fa;
  --red:#e23a3a;
  --ink:#3c4650;
  --muted:#8a939b;
  --line:#dde3e8;
  --white:#ffffff;
  --footer:#2c6aa8;
  --footer-dark:#23588c;
  --strip:#f3f5f7;
}
*{box-sizing:border-box;margin:0;padding:0}
html,body{width:1200px;height:2212px;overflow:hidden}
body{font-family:'Open Sans',Arial,sans-serif;color:var(--ink);background:var(--white);font-size:13px;position:relative}
a{color:inherit;text-decoration:none}

/* top bar */
.topbar{height:40px;background:var(--white);display:flex;align-items:center;justify-content:space-between;padding:0 24px 0 150px;font-size:12px;color:var(--muted)}
.topbar .contact{display:flex;gap:22px;align-items:center}
.topbar .contact svg{vertical-align:-3px;margin-right:5px}
.social{display:flex;gap:7px;align-items:center}
.social span{width:24px;height:24px;border-radius:50%;background:var(--blue)}
.search{width:130px;height:24px;border:1px solid var(--line);border-radius:12px;margin-left:10px;display:flex;align-items:center;justify-content:flex-end;padding-right:8px}

/* header + nav */
.header{height:88px;position:relative;background:linear-gradient(var(--white),#f4f7fa);border-bottom:1px solid var(--line)}
.logo{position:absolute;left:18px;top:-32px;width:120px;height:116px;display:flex;flex-direction:column;align-items:center;justify-content:center;gap:6px}
.logo .mark{width:58px;height:58px;background:var(--blue);border-radius:50%}
.logo .name{font-weight:700;font-size:14px;color:var(--blue)}
.nav{position:absolute;left:200px;top:24px;display:flex;height:40px}
.nav a{display:flex;align-items:center;padding:0 17px;font-size:14px;font-weight:600;color:var(--ink);position:relative}
.nav a.active{background:var(--blue);color:var(--white);border-radius:3px}
.nav a.open{background:var(--blue-light);color:var(--white);border-radius:3px 3px 0 0}
.dropdown{position:absolute;left:0;top:40px;width:150px;background:var(--blue-light);border-radius:0 3px 3px 3px;padding:6px 0;z-index:5}
.dropdown span{display:block;padding:5px 14px;font-size:12px;font-weight:400;color:var(--white)}

/* hero */
.hero{height:464px;position:relative;background:linear-gradient(160deg,#8fc0a8 0%,#5e9a6e 40%,#c9b59a 75%,#7a8f63 100%)}
.hero-caption{position:absolute;left:0;bottom:36px}
.hero-caption .line1{display:inline-block;background:var(--blue);color:var(--white);font-size:24px;font-style:italic;font-weight:600;padding:6px 20px}
.hero-caption .line2{display:block;width:max-content;background:rgba(20,30,40,.75);color:var(--white);font-size:28px;font-weight:600;padding:8px 20px;margin-top:6px}
.arrow{position:absolute;top:210px;width:34px;height:44px;background:rgba(31,109,179,.85);display:flex;align-items:center;justify-content:center}
.arrow.left{left:0}.arrow.right{right:0}

/* features */
.features{height:408px;display:flex;justify-content:space-between;padding:40px 100px 0}
.feature{width:300px;text-align:center}
.feature .photo{height:180px;border:1px solid var(--line);padding:6px;background:var(--white)}
.feature .photo div{width:100%;height:100%}
.feature h3{font-size:18px;font-weight:400;margin:18px 0 10px;color:var(--ink)}
.feature p{font-size:12px;line-height:18px;color:var(--muted);padding:0 20px}
.btn{display:inline-block;background:var(--blue);color:var(--white);font-size:12px;font-weight:600;padding:5px 18px;border-radius:2px;margin-top:12px}

/* banner */
.banner{height:80px;margin:8px 80px 0;background:var(--blue-light);display:flex;align-items:center;justify-content:center;color:var(--white);font-size:21px;font-weight:400}

/* services */
.services{margin:40px 80px 0;height:360px;border:1px solid var(--line);padding:24px 40px}
.services h2{text-align:center;font-size:18px;font-style:italic;font-weight:600;color:var(--ink);margin-bottom:34px}
.grid{display:grid;grid-template-columns:repeat(3,1fr);row-gap:48px;column-gap:30px}
.service{display:flex;gap:16px}
.service .icon{width:58px;height:58px;border-radius:50%;flex:none}
.service h4{font-size:14px;font-weight:600;margin-bottom:6px}
.service p{font-size:12px;line-height:17px;color:var(--muted)}

/* education */
.education{height:300px;display:flex;gap:34px;padding:32px 80px 0}
.education .photo{width:380px;height:230px;background:linear-gradient(135deg,#5d6f84,#a9b7c4 55%,#3e4e60)}
.education h2{font-size:24px;font-weight:400;margin-bottom:16px}
.education p{font-size:12px;line-height:20px;color:var(--muted);margin-bottom:12px}

/* footer */
.footer-main{height:180px;background:var(--footer);color:var(--white);display:flex;padding:22px 80px 0;gap:60px}
.footer-main h5{font-size:16px;font-weight:600;margin-bottom:12px}
.footer-main .col{width:320px}
.footer-main p{font-size:12px;line-height:18px;opacity:.9}
.footer-main .btn{background:var(--footer-dark);margin-top:10px}
.quote{font-style:italic}
.contact-row{display:flex;gap:18px;align-items:flex-start}
.contact-row .pin{width:64px;height:64px;border-radius:50%;background:var(--white);display:flex;align-items:center;justify-content:center;flex:none}

.partners{height:92px;background:var(--strip);display:flex;align-items:center;justify-content:space-between;padding:0 90px}
.partners span{width:110px;height:44px;background:#d5dde4;border-radius:4px}

.footer-bottom{height:132px;display:flex;align-items:center;padding:0 80px;gap:120px;font-size:12px;color:var(--muted);border-top:4px solid var(--blue)}
.footer-bottom .logo-s{display:flex;align-items:center;gap:10px;font-weight:700;color:var(--blue);font-size:15px}
.footer-bottom .logo-s span{width:40px;height:40px;border-radius:50%;background:var(--blue)}
.links{display:flex;gap:80px}
.links ul{list-style:none;line-height:20px}
.copy{margin-left:auto;align-self:flex-start;padding-top:32px}
</style>
</head>
<body>

<div class="topbar">
  <div class="contact">
    <span>Contact us</span>
    <span><svg width="12" height="12" viewBox="0 0 24 24"><path fill="#8a939b" d="M6.6 10.8a15 15 0 0 0 6.6 6.6l2.2-2.2c.3-.3.7-.4 1-.2 1.1.4 2.3.6 3.6.6.6 0 1 .4 1 1V20c0 .6-.4 1-1 1A17 17 0 0 1 3 4c0-.6.4-1 1-1h3.5c.6 0 1 .4 1 1 0 1.2.2 2.4.6 3.6.1.3 0 .7-.2 1z"/></svg>+86 400 555 0192</span>
  </div>
  <div class="social">
    <span></span><span></span><span></span><span></span><span></span>
    <div class="search"><svg width="12" height="12" viewBox="0 0 24 24"><circle cx="10" cy="10" r="7" fill="none" stroke="#8a939b" stroke-width="2.5"/><path d="M15 15l6 6" stroke="#8a939b" stroke-width="2.5"/></svg></div>
  </div>
</div>

<header class="header">
  <div class="logo"><div class="mark"></div><div class="name">Tovin Brightway</div></div>
  <nav class="nav">
    <a class="active">Home</a>
    <a>Third space for Diabetics</a>
    <a>Education</a>
    <a class="open">Events
      <div class="dropdown"><span>Upcoming events</span><span>Past events</span><span>Event gallery</span></div>
    </a>
    <a>Franchise</a>
    <a>Infographics</a>
    <a>Low carb diet</a>
    <a>Contact</a>
  </nav>
</header>

<section class="hero" role="img" aria-label="Smiling senior Chinese family outdoors in a green park">
  <div class="hero-caption">
    <span class="line1">Live a long and active life...</span>
    <span class="line2">Take the right kind of food to control Diabetes</span>
  </div>
  <div class="arrow left"><svg width="12" height="18" viewBox="0 0 12 18"><path d="M10 2L3 9l7 7" stroke="#fff" stroke-width="3" fill="none"/></svg></div>
  <div class="arrow right"><svg width="12" height="18" viewBox="0 0 12 18"><path d="M2 2l7 7-7 7" stroke="#fff" stroke-width="3" fill="none"/></svg></div>
</section>

<section class="features">
  <div class="feature">
    <div class="photo"><div role="img" aria-label="Fresh vegetables and healthy food" style="background:linear-gradient(135deg,#d94a3a,#8cbf4a 55%,#f0d27a)"></div></div>
    <h3>3rd space for Diabetics</h3>
    <p>A welcoming place between hospital and home where people with diabetes find food, advice and friendly support every day of the week.</p>
    <a class="btn">Read More</a>
  </div>
  <div class="feature">
    <div class="photo"><div role="img" aria-label="Diabetes facts infographic" style="background:linear-gradient(135deg,#e8eef3,#9ec5e2 60%,#e24a4a)"></div></div>
    <h3>Infographics</h3>
    <p>Clear charts and simple facts that explain blood sugar, healthy meals and daily habits for patients, families and care partners.</p>
    <a class="btn">Read More</a>
  </div>
  <div class="feature">
    <div class="photo"><div role="img" aria-label="Business partners shaking hands" style="background:linear-gradient(135deg,#3b3f48,#c9a88c 55%,#e6e2dc)"></div></div>
    <h3>Business Partnership</h3>
    <p>Join our growing franchise network and bring trusted diabetic care, product knowledge and business support to your own city.</p>
    <a class="btn">Read More</a>
  </div>
</section>

<div class="banner">It is simple to live a normal, healthy life with Diabetes...</div>

<section class="services">
  <h2>" Good Health, Extending Life "</h2>
  <div class="grid">
    <div class="service"><div class="icon" role="img" aria-label="Workshop icon" style="background:#3aa7d9"></div><div><h4>Workshop</h4><p>Hands-on sessions that teach meal planning and daily glucose care.</p></div></div>
    <div class="service"><div class="icon" role="img" aria-label="Education events icon" style="background:#f0a23a"></div><div><h4>Education &amp; Advice Events</h4><p>Regular talks with experts held in cities across China.</p></div></div>
    <div class="service"><div class="icon" role="img" aria-label="Heart health icon" style="background:#e23a3a"></div><div><h4>Diabetes and Heart Health</h4><p>Learn how diabetes affects the heart and how to protect it.</p></div></div>
    <div class="service"><div class="icon" role="img" aria-label="Low carb food icon" style="background:#8cbf4a"></div><div><h4>Low Carb Diabetic</h4><p>Tasty low carb recipes and sugar-free foods for every meal.</p></div></div>
    <div class="service"><div class="icon" role="img" aria-label="Franchise icon" style="background:#e8c23a"></div><div><h4>Franchise</h4><p>Training, supply and know-how for partners opening a new store.</p></div></div>
    <div class="service"><div class="icon" role="img" aria-label="Health care professionals icon" style="background:#5fa8d8"></div><div><h4>Health Care Professionals</h4><p>Doctors and dietitians who guide patients with care and skill.</p></div></div>
  </div>
</section>

<section class="education">
  <div class="photo" role="img" aria-label="Audience attending a diabetes education seminar"></div>
  <div>
    <h2>Recent Education Program</h2>
    <p>Our latest program brought doctors, dietitians and families together for a full day of learning. Guests joined talks on blood sugar control, tried low carb cooking and asked experts their own questions.</p>
    <p>More events are planned across China this year. Stores and partners can book a session, invite local patients and receive full training material from our team.</p>
  </div>
</section>

<footer>
  <div class="footer-main">
    <div class="col">
      <h5>About Us</h5>
      <p>We are the third space for diabetics, linking hospital and home with food, advice and care.</p>
      <a class="btn">Read More</a>
    </div>
    <div class="col">
      <h5>Testimonials</h5>
      <p class="quote">“ The events helped my father understand his diet. The staff are kind and truly professional. ”</p>
    </div>
    <div class="col">
      <h5>Contact Us</h5>
      <div class="contact-row">
        <div class="pin"><svg width="26" height="34" viewBox="0 0 24 32"><path d="M12 0a11 11 0 0 0-11 11c0 8 11 21 11 21s11-13 11-21A11 11 0 0 0 12 0z" fill="#2c6aa8"/><circle cx="12" cy="11" r="4" fill="#fff"/></svg></div>
        <p>+86 400 555 0192<br>info@tovinbrightway.com<br>Shanghai, China</p>
      </div>
    </div>
  </div>

  <div class="partners" aria-label="Partners">
    <span></span><span></span><span></span><span></span><span></span><span></span><span></span>
  </div>

  <div class="footer-bottom">
    <div class="logo-s"><span></span>Tovin Brightway</div>
    <div class="links">
      <ul><li>Home</li><li>Low carb diet</li><li>Education Programs</li><li>Events</li></ul>
      <ul><li>Franchise</li><li>Infographics</li><li>Third space for Diabetics</li><li>Contact</li></ul>
    </div>
    <div class="copy">© 2014 Tovin Brightway, All Rights Reserved</div>
  </div>
</footer>

</body>
</html>
```